Business Card Design

Just looking for a good designs that looks good with our company logo. I'd like it to be simple and to the point. Just including contact information, our logo, and my name somewhere on the card so future clients know who they're contacting, and a couple services offered. The two images I attached are pictures of our logo. I don't care which color they they are, I just attached both images to give a reference of logo colors depending on the color of the card.
Names: Carl Whitby
Phone: 816-555-0147
Email: greenstripeyard@fernmail.test
Services offered:
Mowing
Fertilization
Aeration
Bed & tree maintenance
and more.
Business
Names: Carl Whitby
Phone: 816-555-0147
(no website)

```html
<!DOCTYPE html>
<html lang="en">
<head>
<meta charset="utf-8">
<title>Greenstripe Yard Care – Business Card</title>
<link rel="stylesheet" href="https://fonts.googleapis.com/css2?family=Lato:wght@400;700;900&display=swap">
<style>
  :root {
    --backdrop: #2b2b2d;
    --card-white: #f7f7f7;
    --brand-red: #e0462f;
    --brand-red-deep: #c93a26;
    --brand-navy: #2c3146;
    --service-text: #ecd6cf;
    --ink: #1d1d1f;
  }
  html, body {
    margin: 0;
    width: 1200px;
    height: 900px;
    overflow: hidden;
    background: var(--backdrop);
    font-family: "Lato", Arial, sans-serif;
  }
  .card {
    position: absolute;
    left: 75px;
    top: 150px;
    width: 1050px;
    height: 600px;
    background: var(--card-white);
    overflow: hidden;
  }
  .card-shapes {
    position: absolute;
    inset: 0;
  }
  .brand {
    position: absolute;
    left: 70px;
    top: 225px;
    width: 440px;
    display: flex;
    align-items: center;
    gap: 18px;
  }
  .brand-dot {
    flex: none;
    width: 54px;
    height: 54px;
    border-radius: 50%;
    background: var(--brand-red);
  }
  .brand-name {
    margin: 0;
    font-size: 44px;
    font-weight: 900;
    line-height: 1.05;
    color: var(--brand-navy);
    text-transform: uppercase;
  }
  .contact {
    position: absolute;
    left: 610px;
    top: 55px;
  }
  .contact-name {
    margin: 0;
    font-size: 30px;
    font-weight: 900;
    color: var(--brand-navy);
    letter-spacing: 0.5px;
  }
  .contact-role {
    margin: 2px 0 0;
    font-size: 18px;
    font-weight: 700;
    color: var(--brand-red);
    text-transform: uppercase;
  }
  .contact-list {
    list-style: none;
    margin: 24px 0 0 -10px;
    padding: 0;
  }
  .contact-item {
    display: flex;
    align-items: center;
    gap: 14px;
    font-size: 22px;
    font-weight: 700;
    color: var(--ink);
    margin-bottom: 10px;
  }
  .contact-icon { width: 24px; height: 20px; flex: none; }
  .services {
    position: absolute;
    left: 575px;
    top: 405px;
    margin: 0;
    font-size: 29px;
    font-weight: 700;
    line-height: 1.3;
    color: var(--service-text);
  }
  .services-tag {
    position: absolute;
    left: 120px;
    top: 505px;
    padding: 12px 32px;
    background: var(--brand-navy);
    color: #f2f2f2;
    font-size: 30px;
    font-weight: 700;
    letter-spacing: 0.5px;
  }
</style>
</head>
<body>
  <article class="card">
    <svg class="card-shapes" viewBox="0 0 1050 600" width="1050" height="600" aria-hidden="true">
      <defs>
        <linearGradient id="redFill" x1="0" y1="0" x2="1" y2="1">
          <stop offset="0" stop-color="#e0462f"/>
          <stop offset="1" stop-color="#c93a26"/>
        </linearGradient>
      </defs>
      <path class="wave-navy" fill="#2c3146"
            d="M0 440 C 300 470 500 385 690 330 S 950 275 1050 280 L1050 600 L0 600 Z"/>
      <path class="wave-red" fill="url(#redFill)" stroke="#f7f7f7" stroke-width="8"
            d="M0 472 C 300 502 500 417 690 362 S 950 307 1050 312 L1060 610 L-10 610 Z"/>
    </svg>

    <div class="brand">
      <span class="brand-dot"></span>
      <p class="brand-name">Greenstripe<br>Yard Care</p>
    </div>

    <section class="contact">
      <h1 class="contact-name">CARL WHITBY</h1>
      <p class="contact-role">Designation</p>
      <ul class="contact-list">
        <li class="contact-item">
          <svg class="contact-icon" viewBox="0 0 26 22" aria-hidden="true">
            <path fill="#1d1d1f" d="M2 6 C2 2 24 2 24 6 L24 8 L18 8 L18 6 L8 6 L8 8 L2 8 Z"/>
            <rect x="5" y="10" width="16" height="10" rx="2" fill="#1d1d1f"/>
            <circle cx="13" cy="15" r="3" fill="#f7f7f7"/>
          </svg>
          <span>816-555-0147</span>
        </li>
        <li class="contact-item">
          <svg class="contact-icon" viewBox="0 0 26 22" aria-hidden="true">
            <rect x="1" y="3" width="24" height="16" fill="#1d1d1f"/>
            <path d="M1 3 L13 12 L25 3" fill="none" stroke="#f7f7f7" stroke-width="2"/>
          </svg>
          <span>greenstripeyard@fernmail.test</span>
        </li>
      </ul>
    </section>

    <p class="services">Mowing / Fertilization / Aeration<br>Bed &amp; tree Maintenance &amp; more.</p>
    <div class="services-tag">SERVICES OFFERED</div>
  </article>
</body>
</html>
```